Meadowlark Property Review is a leading provider of residential appraisal and home inspection products in S

I need a business card/logo designed that obviously describes my business. We are a residential appraisal and home inspection company in Springfield, MO. We offer residential appraisals, home inspection, pest inspection and radon gas measurement. We have been in business for 18 years and hold state certified residential appraisal licenses and OBREX certified home inspection licenses. I have a logo that I really like and will attach, but would be open to new suggestions. I like more modern designs than traditional and would like a two sided card with our services, licenses and qualifications on the back.

```html
<!DOCTYPE html>
<html lang="en">
<head>
<meta charset="utf-8">
<title>Meadowlark Property Review – Business Card</title>
<link rel="stylesheet" href="https://fonts.googleapis.com/css2?family=Source+Sans+3:ital,wght@0,400;0,600;1,400&display=swap">
<style>
  :root {
    --backdrop: #3a3a3a;
    --paper: #f8f8f8;
    --brown: #8c6a43;
    --orange: #ee8a1d;
    --ink: #4a4a4a;
    --white: #ffffff;
  }
  * { margin: 0; padding: 0; box-sizing: border-box; }
  html, body { width: 1200px; height: 750px; overflow: hidden; }
  body {
    background: var(--backdrop);
    font-family: "Source Sans 3", sans-serif;
    position: relative;
  }
  .card {
    position: absolute;
    top: 228px;
    width: 461px;
    height: 262px;
    overflow: hidden;
  }
  .card-front { left: 124px; background: var(--paper); }
  .card-back { left: 618px; background: var(--orange); }

  .front-swoosh { position: absolute; inset: 0; }

  .brand-name {
    position: absolute;
    left: 32px;
    top: 62px;
    display: flex;
    align-items: center;
    gap: 8px;
    font-size: 19px;
    font-weight: 600;
    color: var(--brown);
  }
  .brand-square { width: 12px; height: 12px; background: var(--orange); }

  .address {
    position: absolute;
    left: 32px;
    top: 124px;
    font-size: 11.5px;
    line-height: 14.5px;
    color: var(--ink);
  }
  .contacts {
    position: absolute;
    left: 32px;
    top: 162px;
    list-style: none;
    font-size: 11.5px;
    color: var(--ink);
  }
  .contacts li {
    display: flex;
    align-items: center;
    gap: 6px;
    height: 17.6px;
  }
  .contacts svg { width: 13px; height: 13px; fill: var(--brown); }

  .holder {
    position: absolute;
    right: 25px;
    top: 200px;
    text-align: right;
  }
  .holder-name { font-size: 16.5px; font-weight: 600; color: var(--orange); line-height: 20px; }
  .holder-title { font-size: 12.5px; color: var(--white); line-height: 18px; }

  .back-name {
    position: absolute;
    left: 0; right: 0;
    top: 112px;
    text-align: center;
    font-size: 24px;
    font-weight: 600;
    color: var(--white);
  }
  .services {
    position: absolute;
    left: 0; right: 0;
    top: 199px;
    text-align: center;
    font-size: 12px;
    font-style: italic;
    line-height: 18px;
    color: var(--white);
  }
</style>
</head>
<body>
  <section class="card card-front">
    <svg class="front-swoosh" viewBox="0 0 461 262" preserveAspectRatio="none" aria-hidden="true">
      <path d="M458,0 C428,140 300,250 108,262 L461,262 L461,0 Z" fill="var(--orange)"/>
      <path d="M461,4 C434,146 310,252 128,262 L461,262 Z" fill="var(--brown)"/>
    </svg>

    <div class="brand-name"><span class="brand-square"></span>Meadowlark Property Review</div>

    <p class="address">214 Larkspur Court<br>Springfield, Missouri 65804</p>

    <ul class="contacts">
      <li><svg viewBox="0 0 16 16"><path d="M3 1l3 3-1.5 2c1 2 3 4 5 5l2-1.5 3 3-2 2C6 14 2 10 1 3z"/></svg>417 555 0182</li>
      <li><svg viewBox="0 0 16 16"><path d="M4 1h8v4H4zM1 6h14v6h-3v3H4v-3H1zM5 10v4h6v-4z"/></svg>417 555 0147</li>
      <li><svg viewBox="0 0 16 16"><path d="M1 3h14v10H1zM2 4l6 5 6-5v1L8 10 2 5z" fill-rule="evenodd"/></svg>dana@meadowlarkreview.com</li>
      <li><svg viewBox="0 0 16 16"><path d="M8 1a7 7 0 1 1 0 14A7 7 0 0 1 8 1zm-2 3c-1 1-2 2-1 4l2 1v3l2 1 1-3 2-1-1-2-2 0-1-2z" fill-rule="evenodd"/></svg>www.meadowlarkreview.com</li>
    </ul>

    <div class="holder">
      <p class="holder-name">Dana Whitfield</p>
      <p class="holder-title">CEO/Founder</p>
    </div>
  </section>

  <section class="card card-back">
    <p class="back-name">Meadowlark Property Review</p>
    <p class="services">Residential appraisals • Home inspection<br>Pest inspection and radon gas measurement.</p>
  </section>
</body>
</html>
```